Local Flower Farm Needs Business Card Design

I need business cards designed for a flower farm based in Eudora, Kansas.
Business Info:
We are a local cut flower farm located in Eudora, Kansas, founded by Corinne Haldwick. What started as a passion for agriculture and search for more joy in daily life has blossomed into a small business dedicated to providing the community with beautiful, fresh, and sustainable flowers. We specialize in local, seasonal blooms, ensuring that every petal reflects the care and dedication we pour into our craft. Our mission is to deliver the highest quality flowers directly to our customers through local farmers markets and to florists who share our commitment to sustainability. Join us in celebrating the beauty of nature, one bloom at a time!
Contact Details:
Corinne Haldwick
Owner
Phone 913-555-0147
Facebook: Rosalind Thorpe Gardens
Instagram: @RosalindThorpeGardens
Website: RosalindThorpeGardens.example
Target Market(s)
Wholesale to Florists and Direct to Consumer via Farmers Market
Industry/Entity Type
Florist, Farm
Contact Information for Business Card
Name, Contact Info, Logo
Look and feel
Each slider illustrates characteristics of the customer's brand and the style your logo design should communicate.

```html
<!DOCTYPE html>
<html lang="en">
<head>
<meta charset="utf-8">
<title>Rosalind Thorpe Gardens – Business Card</title>
<link href="https://fonts.googleapis.com/css2?family=Libre+Baskerville:wght@400;700&display=swap" rel="stylesheet">
<style>
  :root {
    --stage: #2e2e2f;
    --card: #0c272b;
    --card-edge: #113238;
    --ink: #f4f3ee;
    --ink-soft: rgba(244, 243, 238, 0.75);
    --rule: rgba(244, 243, 238, 0.55);
    --emboss: #15444a;
  }
  * { box-sizing: border-box; margin: 0; padding: 0; }
  html, body {
    width: 1200px; height: 689px; overflow: hidden;
    background: var(--stage);
    font-family: "Libre Baskerville", Georgia, serif;
  }
  .stage {
    position: relative; width: 1200px; height: 689px;
    display: flex; align-items: center; justify-content: center; gap: 40px;
  }
  .card {
    position: relative; width: 540px; height: 309px;
    background: var(--card); border-radius: 22px;
    border: 1px solid var(--card-edge);
    overflow: hidden;
  }
  /* back side */
  .card-back .mark {
    position: absolute; left: 50%; top: 50%;
    width: 170px; height: 170px; margin: -85px 0 0 -85px;
    border: 1px solid var(--emboss); border-radius: 50%;
    display: flex; align-items: center; justify-content: center; text-align: center;
    color: var(--emboss); font-size: 15px; line-height: 1.5; letter-spacing: 2px;
    text-transform: uppercase;
  }
  /* front side */
  .card-front .mark {
    position: absolute; left: 95px; top: 75px;
    width: 160px; height: 160px;
    border: 1px solid var(--rule); border-radius: 50%;
    display: flex; align-items: center; justify-content: center; text-align: center;
    color: var(--ink); font-size: 14px; line-height: 1.55; letter-spacing: 2px;
    text-transform: uppercase;
  }
  .divider {
    position: absolute; left: 292px; top: 78px;
    width: 1px; height: 154px; background: var(--rule);
  }
  .details {
    position: absolute; left: 310px; top: 86px; color: var(--ink);
  }
  .details .name { font-size: 21px; font-weight: 700; letter-spacing: 0.2px; }
  .details .role { font-size: 11.5px; color: var(--ink-soft); margin: 6px 0 12px; }
  .contacts { list-style: none; }
  .contacts li {
    display: flex; align-items: center; gap: 7px;
    font-size: 11.5px; line-height: 1; margin-bottom: 9px; white-space: nowrap;
  }
  .icon { width: 12px; height: 12px; flex: none; }
  .dot { width: 11px; height: 11px; border-radius: 50%; background: var(--ink); flex: none; }
  .square { width: 11px; height: 11px; border-radius: 2px; background: var(--ink); flex: none; }
</style>
</head>
<body>
<main class="stage">
  <section class="card card-back" aria-label="Card back">
    <div class="mark">Rosalind<br>Thorpe<br>Gardens</div>
  </section>

  <section class="card card-front" aria-label="Card front">
    <div class="mark">Rosalind<br>Thorpe<br>Gardens</div>
    <div class="divider"></div>
    <div class="details">
      <p class="name">Corinne Haldwick</p>
      <p class="role">Owner</p>
      <ul class="contacts">
        <li>
          <svg class="icon" viewBox="0 0 24 24" aria-hidden="true"><path fill="#f4f3ee" d="M6.6 10.8a15.1 15.1 0 0 0 6.6 6.6l2.2-2.2a1 1 0 0 1 1-.25 11.4 11.4 0 0 0 3.6.57 1 1 0 0 1 1 1V20a1 1 0 0 1-1 1A17 17 0 0 1 3 4a1 1 0 0 1 1-1h3.5a1 1 0 0 1 1 1c0 1.25.2 2.45.57 3.57a1 1 0 0 1-.25 1z"/></svg>
          913-555-0147
        </li>
        <li><span class="square"></span>Rosalind Thorpe Gardens</li>
        <li><span class="dot"></span>@RosalindThorpeGardens</li>
        <li>
          <svg class="icon" viewBox="0 0 24 24" aria-hidden="true"><circle cx="12" cy="12" r="10" fill="none" stroke="#f4f3ee" stroke-width="2"/><path d="M2 12h20M12 2a15 15 0 0 1 0 20M12 2a15 15 0 0 0 0 20" fill="none" stroke="#f4f3ee" stroke-width="1.6"/></svg>
          RosalindThorpeGardens.example
        </li>
      </ul>
    </div>
  </section>
</main>
</body>
</html>
```